Stonebrace Business Card Design

The Stonebrace Co is an aggregate (crushing) equipment dealer serving Western Canadian provinces. Stonebrace is a distributor of aggregate equipment for different manufacturers.

We are looking to change and update the existing business card which has been used since the existence of the company. A copy of existing card has been attached for reference. The Stonebrace Co logo we want to remain the same and we want the green color to remain the same.

We are wanting something new with a different look. A refreshing card to show a new modern and updated look. No longer wanting to have the manufacturers on the back of the card but something more like our logo on the back of the card with a statement like "Crushing Solutions"

ideas could be:
- card can be different colors on front and back
- front or reverse of the card could possibly be the green color with the logo in black

Target Market(s)

Owners of Aggregate/Crushing companies

Contact Information for Business Card

see above

Requirements
Must have
• - logo to remain same along with same font within logo
• - green color to remain same
Nice to have
• as noted above under project description
Should not have

```html
<!DOCTYPE html>
<html lang="en">
<head>
<meta charset="utf-8">
<title>Stonebrace Co – Business Card</title>
<link href="https://fonts.googleapis.com/css2?family=Arimo:wght@400;700&display=swap" rel="stylesheet">
<style>
  :root {
    --stage: #000000;
    --card-light: #f3f3f3;
    --brand-green: #8b8b0a;
    --brand-green-deep: #7b7b07;
    --ink: #1b1b1b;
    --paper-white: #ffffff;
  }
  * { margin: 0; padding: 0; box-sizing: border-box; }
  html, body {
    width: 1200px; height: 900px; overflow: hidden;
    background: var(--stage);
    font-family: "Arimo", Arial, sans-serif;
  }
  .stage { position: relative; width: 1200px; height: 900px; }

  .card { position: absolute; top: 200px; width: 310px; height: 502px; overflow: hidden; }

  .card-front {
    left: 265px;
    background: var(--card-light);
    border-radius: 62px 0 62px 0;
  }
  .brand-name {
    position: absolute; top: 167px; left: 0; width: 100%; text-align: center;
    font-weight: 700; font-size: 19px; line-height: 22px; color: var(--ink); letter-spacing: 0.2px;
  }
  .contact { position: absolute; left: 25px; top: 286px; }
  .contact-name {
    font-size: 19px; line-height: 22px; color: var(--brand-green); letter-spacing: 0.3px; margin-bottom: 13px;
  }
  .contact-list { list-style: none; }
  .contact-list li {
    display: flex; align-items: center; gap: 8px; margin-left: 2px;
    font-size: 14.5px; line-height: 18px; color: var(--ink);
  }
  .contact-list svg { width: 11px; height: 11px; fill: var(--brand-green); flex: none; }
  .address { margin-top: 10px; margin-left: 3px; font-size: 14.5px; line-height: 18px; color: var(--ink); font-style: normal; }

  .card-back {
    left: 641px;
    border-radius: 0 62px 0 62px;
  }
  .back-surface {
    position: absolute; inset: 0;
    background: linear-gradient(160deg, var(--brand-green) 0%, var(--brand-green-deep) 50%, var(--brand-green) 100%);
  }
  .back-brand {
    position: absolute; top: 230px; left: 0; width: 100%; text-align: center;
    font-weight: 700; font-size: 34px; line-height: 40px; color: var(--paper-white); letter-spacing: 1px;
  }
  .tagline {
    position: absolute; top: 426px; left: 0; width: 100%; text-align: center;
    font-weight: 700; font-size: 14.5px; line-height: 18px; color: var(--paper-white); letter-spacing: 3.6px;
    padding-left: 3.6px;
  }
</style>
</head>
<body>
<main class="stage">

  <section class="card card-front">
    <p class="brand-name">THE STONEBRACE CO.</p>

    <div class="contact">
      <p class="contact-name">GAVIN MORELAND</p>
      <ul class="contact-list">
        <li><svg viewBox="0 0 12 12"><path d="M1 4c0-2 2-3 5-3s5 1 5 3l-3 1-1-1H5L4 5zM2 6h8l1 5H1z"/></svg>780.555.0148(Direct)</li>
        <li><svg viewBox="0 0 12 12"><path d="M1 4c0-2 2-3 5-3s5 1 5 3l-3 1-1-1H5L4 5zM2 6h8l1 5H1z"/></svg>780.555.0172</li>
        <li><svg viewBox="0 0 12 12"><path d="M3 1h5l2 2v2h1v6H1V5h2zM4 2v3h5V3.5L7.5 2zM3 7v2h6V7z"/></svg>780.555.0193</li>
        <li><svg viewBox="0 0 12 12"><path d="M1 3h10v1L6 7 1 4zM1 5l5 3 5-3v5H1z"/></svg>gavin@stonebr.com</li>
        <li><svg viewBox="0 0 12 12"><circle cx="6" cy="6" r="5"/></svg>www.stonebrace.ca</li>
      </ul>
      <address class="address">2218-48B Avenue<br>Nisku, Alberta T9E 4K1</address>
    </div>
  </section>

  <section class="card card-back">
    <div class="back-surface" role="img" aria-label="Soft flowing green background in two shades of brand green"></div>
    <p class="back-brand">STONEBRACE</p>
    <p class="tagline">CRUSHING SOLUTIONS</p>
  </section>

</main>
</body>
</html>
```